Step and Repeat Backdrop for wedding reception photo booth

Would like to have a Step and Repeat Backdrop (8 foot high by 10 foot wide) that incorporates the wedding logo (attached) and the names Helen and Gavin. Background should be white, and wedding colors are burgundy and gold. Show me creativity :-) I have included some random samples.

```html
<!DOCTYPE html>
<html lang="en">
<head>
<meta charset="utf-8">
<title>Helen &amp; Gavin — Step and Repeat Backdrop</title>
<link rel="stylesheet" href="https://fonts.googleapis.com/css2?family=Playfair+Display:wght@500&display=swap">
<style>
  :root {
    --gold: #b5a030;
    --paper: #ffffff;
    --stage: #f2f2f0;
    --shadow: rgba(0, 0, 0, 0.45);
  }
  html, body {
    margin: 0;
    padding: 0;
    width: 1200px;
    height: 660px;
    overflow: hidden;
    background: var(--stage);
  }
  .canvas {
    position: relative;
    width: 1200px;
    height: 660px;
  }
  .backdrop {
    position: absolute;
    left: 210px;
    top: 20px;
    width: 780px;
    height: 620px;
    background: var(--paper);
    overflow: hidden;
    box-shadow: 10px 12px 22px var(--shadow);
    font-family: "Playfair Display", serif;
    color: var(--gold);
  }
  .band {
    position: absolute;
    left: 0;
    width: 100%;
    height: 26px;
    background: var(--gold);
  }
  .band--top { top: 0; }
  .band--bottom { bottom: 0; }
  .repeat {
    position: absolute;
    transform: translate(-50%, -50%);
    font-size: 30px;
    font-weight: 500;
    letter-spacing: -2px;
    line-height: 1;
    white-space: nowrap;
  }
  .monogram {
    position: absolute;
    left: 389px;
    top: 311px;
    transform: translate(-50%, -50%);
    font-size: 96px;
    font-weight: 500;
    letter-spacing: -6px;
    line-height: 1;
    white-space: nowrap;
  }
</style>
</head>
<body>
<main class="canvas">
  <section class="backdrop" aria-label="Helen and Gavin step and repeat backdrop">
    <div class="band band--top"></div>
    <div class="band band--bottom"></div>

    <!-- column 1 -->
    <span class="repeat" style="left:31px;top:78px">H&amp;G</span>
    <span class="repeat" style="left:31px;top:144px">H&amp;G</span>
    <span class="repeat" style="left:31px;top:211px">H&amp;G</span>
    <span class="repeat" style="left:31px;top:276px">H&amp;G</span>
    <span class="repeat" style="left:31px;top:343px">H&amp;G</span>
    <span class="repeat" style="left:31px;top:409px">H&amp;G</span>
    <span class="repeat" style="left:31px;top:475px">H&amp;G</span>
    <span class="repeat" style="left:31px;top:541px">H&amp;G</span>

    <!-- column 2 -->
    <span class="repeat" style="left:121px;top:51px">H&amp;G</span>
    <span class="repeat" style="left:121px;top:116px">H&amp;G</span>
    <span class="repeat" style="left:121px;top:181px">H&amp;G</span>
    <span class="repeat" style="left:121px;top:246px">H&amp;G</span>
    <span class="repeat" style="left:121px;top:311px">H&amp;G</span>
    <span class="repeat" style="left:121px;top:376px">H&amp;G</span>
    <span class="repeat" style="left:121px;top:439px">H&amp;G</span>
    <span class="repeat" style="left:121px;top:504px">H&amp;G</span>
    <span class="repeat" style="left:121px;top:569px">H&amp;G</span>

    <!-- column 3 -->
    <span class="repeat" style="left:211px;top:78px">H&amp;G</span>
    <span class="repeat" style="left:211px;top:144px">H&amp;G</span>
    <span class="repeat" style="left:211px;top:211px">H&amp;G</span>
    <span class="repeat" style="left:211px;top:276px">H&amp;G</span>
    <span class="repeat" style="left:211px;top:343px">H&amp;G</span>
    <span class="repeat" style="left:211px;top:409px">H&amp;G</span>
    <span class="repeat" style="left:211px;top:475px">H&amp;G</span>
    <span class="repeat" style="left:211px;top:541px">H&amp;G</span>

    <!-- column 4 -->
    <span class="repeat" style="left:299px;top:51px">H&amp;G</span>
    <span class="repeat" style="left:299px;top:116px">H&amp;G</span>
    <span class="repeat" style="left:299px;top:181px">H&amp;G</span>
    <span class="repeat" style="left:299px;top:439px">H&amp;G</span>
    <span class="repeat" style="left:299px;top:504px">H&amp;G</span>
    <span class="repeat" style="left:299px;top:569px">H&amp;G</span>

    <!-- column 5 -->
    <span class="repeat" style="left:389px;top:78px">H&amp;G</span>
    <span class="repeat" style="left:389px;top:144px">H&amp;G</span>
    <span class="repeat" style="left:389px;top:475px">H&amp;G</span>
    <span class="repeat" style="left:389px;top:541px">H&amp;G</span>

    <!-- column 6 -->
    <span class="repeat" style="left:478px;top:51px">H&amp;G</span>
    <span class="repeat" style="left:478px;top:116px">H&amp;G</span>
    <span class="repeat" style="left:478px;top:181px">H&amp;G</span>
    <span class="repeat" style="left:478px;top:439px">H&amp;G</span>
    <span class="repeat" style="left:478px;top:504px">H&amp;G</span>
    <span class="repeat" style="left:478px;top:569px">H&amp;G</span>

    <!-- column 7 -->
    <span class="repeat" style="left:567px;top:78px">H&amp;G</span>
    <span class="repeat" style="left:567px;top:144px">H&amp;G</span>
    <span class="repeat" style="left:567px;top:211px">H&amp;G</span>
    <span class="repeat" style="left:567px;top:276px">H&amp;G</span>
    <span class="repeat" style="left:567px;top:343px">H&amp;G</span>
    <span class="repeat" style="left:567px;top:409px">H&amp;G</span>
    <span class="repeat" style="left:567px;top:475px">H&amp;G</span>
    <span class="repeat" style="left:567px;top:541px">H&amp;G</span>

    <!-- column 8 -->
    <span class="repeat" style="left:657px;top:51px">H&amp;G</span>
    <span class="repeat" style="left:657px;top:116px">H&amp;G</span>
    <span class="repeat" style="left:657px;top:181px">H&amp;G</span>
    <span class="repeat" style="left:657px;top:246px">H&amp;G</span>
    <span class="repeat" style="left:657px;top:311px">H&amp;G</span>
    <span class="repeat" style="left:657px;top:376px">H&amp;G</span>
    <span class="repeat" style="left:657px;top:439px">H&amp;G</span>
    <span class="repeat" style="left:657px;top:504px">H&amp;G</span>
    <span class="repeat" style="left:657px;top:569px">H&amp;G</span>

    <!-- column 9 -->
    <span class="repeat" style="left:752px;top:78px">H&amp;G</span>
    <span class="repeat" style="left:752px;top:144px">H&amp;G</span>
    <span class="repeat" style="left:752px;top:211px">H&amp;G</span>
    <span class="repeat" style="left:752px;top:276px">H&amp;G</span>
    <span class="repeat" style="left:752px;top:343px">H&amp;G</span>
    <span class="repeat" style="left:752px;top:409px">H&amp;G</span>
    <span class="repeat" style="left:752px;top:475px">H&amp;G</span>
    <span class="repeat" style="left:752px;top:541px">H&amp;G</span>

    <h1 class="monogram" style="margin:0">H&amp;G</h1>
  </section>
</main>
</body>
</html>
```